Business Card for Coastal Tundrabridge Advisory

We need a business card for Coastal Tundrabridge Advisory. The company website address is provided below. The company logo is attached. We provide specialized permafrost services to the mining, transportation, and oil & gas industries. The card should be prepared for:
Matthias Korhonen, PhD.
Coastal Tundrabridge Advisory
PO Box 418259
Quillwater, Alaska 99642
Direct: +1-907-555-0143
Email: mkorhonen@tundrabridgeadvisory.example
Website: www.coastaltundrabridgeadvisory.example

```html
<!DOCTYPE html>
<html lang="en">
<head>
<meta charset="utf-8">
<title>Coastal Tundrabridge Advisory – Business Card</title>
<link rel="stylesheet" href="https://fonts.googleapis.com/css2?family=Montserrat:wght@400;500;700&display=swap">
<style>
  :root {
    --navy: #131a24;
    --paper: #ffffff;
    --ink: #131a24;
    --backdrop: #3b3c3e;
    --mark-on-navy: #2c3a52;
  }
  * { margin: 0; padding: 0; box-sizing: border-box; }
  html, body { width: 1200px; height: 1200px; overflow: hidden; }
  body {
    background: var(--backdrop);
    font-family: "Montserrat", sans-serif;
    display: flex;
    flex-direction: column;
    align-items: center;
    justify-content: center;
    gap: 60px;
  }
  .card {
    position: relative;
    width: 860px;
    height: 491px;
    border-radius: 32px;
    overflow: hidden;
  }
  .card--back {
    background: var(--navy);
    display: flex;
    align-items: center;
    justify-content: center;
  }
  .back-mark {
    font-weight: 500;
    font-size: 40px;
    letter-spacing: 0.06em;
    text-transform: uppercase;
    color: var(--mark-on-navy);
    text-align: center;
    line-height: 1.3;
  }
  .card--front { background: var(--paper); color: var(--ink); }
  .wave { position: absolute; inset: 0; width: 100%; height: 100%; }
  .front-mark {
    position: absolute;
    left: 48px;
    top: 218px;
    width: 300px;
    font-weight: 500;
    font-size: 24px;
    letter-spacing: 0.04em;
    text-transform: uppercase;
    line-height: 1.3;
    color: var(--ink);
  }
  .divider {
    position: absolute;
    left: 372px;
    top: 92px;
    width: 2px;
    height: 270px;
    background: var(--ink);
  }
  .details {
    position: absolute;
    left: 398px;
    top: 86px;
  }
  .person-name { font-weight: 700; font-size: 30px; line-height: 1.1; }
  .person-title { font-size: 19px; margin-top: 4px; }
  .address { font-size: 19px; line-height: 1.3; margin-top: 16px; }
  .contacts { list-style: none; margin-top: 16px; font-size: 18px; }
  .contacts li { display: flex; align-items: center; gap: 12px; height: 32px; }
  .contacts svg { width: 18px; height: 18px; flex: none; fill: var(--ink); }
</style>
</head>
<body>
  <section class="card card--back" aria-label="Card back">
    <p class="back-mark">Coastal Tundrabridge<br>Advisory</p>
  </section>

  <section class="card card--front" aria-label="Card front">
    <svg class="wave" viewBox="0 0 860 491" preserveAspectRatio="none" aria-hidden="true">
      <path d="M0,491 V478 C170,418 400,418 590,402 C730,390 815,360 860,300 V491 Z" fill="var(--navy)"/>
      <path d="M110,452 C270,420 440,422 600,410 C730,400 812,375 860,322" fill="none" stroke="var(--paper)" stroke-width="4"/>
    </svg>

    <p class="front-mark">Coastal Tundrabridge<br>Advisory</p>
    <div class="divider"></div>

    <div class="details">
      <h1 class="person-name">Matthias Korhonen, PhD.</h1>
      <p class="person-title">Managing Director</p>
      <p class="address">PO Box 418259<br>Quillwater, Alaska 99642</p>
      <ul class="contacts">
        <li>
          <svg viewBox="0 0 24 24" aria-hidden="true"><path d="M6.6 10.8a15.1 15.1 0 0 0 6.6 6.6l2.2-2.2a1 1 0 0 1 1-.25 11.4 11.4 0 0 0 3.6.57 1 1 0 0 1 1 1V20a1 1 0 0 1-1 1A17 17 0 0 1 3 4a1 1 0 0 1 1-1h3.5a1 1 0 0 1 1 1c0 1.25.2 2.45.57 3.57a1 1 0 0 1-.25 1z"/></svg>
          +1-907-555-0143
        </li>
        <li>
          <svg viewBox="0 0 24 24" aria-hidden="true"><path d="M2 5h20v14H2z M2 5l10 8 10-8" /><path d="M3 6l9 7 9-7" fill="none" stroke="#fff" stroke-width="1.6"/></svg>
          mkorhonen@tundrabridgeadvisory.example
        </li>
        <li>
          <svg viewBox="0 0 24 24" aria-hidden="true"><circle cx="12" cy="12" r="10"/><path d="M2 12h20M12 2c3 3 3 17 0 20M12 2c-3 3-3 17 0 20" fill="none" stroke="#fff" stroke-width="1.4"/></svg>
          www.coastaltundrabridgeadvisory.example
        </li>
      </ul>
    </div>
  </section>
</body>
</html>
```